Boutique custom software development company needs new business card

Our nearly 20 year old custom software development company would like to better include the fact that we are now providing Bitcoin services. These new services are B2B include education (how to acquire and securely hold Bitcoin) and integrating Bitcoin payments into existing ecommerce sites or other existing systems. Please keep the card clean and simple. Attached is our current design and some other files. vextorial.com

Target Market(s)

businesses owners interested in long term relationship

Industry/Entity Type

Custom software development and Bitcoin

Contact Information for Business Card

Dale Parker, dale@vextorial.com, vextorial.com, (888) 555-VXTRL

Font styles to use
Other font styles liked:
• monospace

Requirements
Must have
• double-sided
Nice to have
• clean and simple
Should not have
• physical address

```html
<!DOCTYPE html>
<html lang="en">
<head>
<meta charset="utf-8">
<title>Vextorial business card</title>
<link rel="stylesheet" href="https://fonts.googleapis.com/css2?family=Lato:wght@400&family=Montserrat:wght@800&family=Arimo:wght@400&family=IBM+Plex+Mono:wght@500&display=swap">
<style>
  :root {
    --blue: #3361a2;
    --blue-deep: #2c5593;
    --orange: #dd6a1e;
    --paper: #f4f4f2;
    --ink: #2b2b2b;
    --tagline: #dfe6f0;
    --backdrop: #2a2a2c;
  }
  * { margin: 0; padding: 0; box-sizing: border-box; }
  html, body {
    width: 1200px; height: 874px; overflow: hidden;
    background: var(--backdrop);
  }
  .canvas { position: relative; width: 1200px; height: 874px; }
  .card {
    position: absolute; left: 290px; width: 620px; height: 354px;
    overflow: hidden;
  }
  .card--front { top: 68px; background: var(--blue); }
  .card--back { top: 452px; background: var(--paper); }

  .brand {
    position: absolute; left: 0; right: 0; top: 104px;
    text-align: center; color: #ffffff;
  }
  .brand__name {
    font-family: "Montserrat", sans-serif; font-weight: 800;
    font-size: 64px; letter-spacing: 1px; line-height: 1;
  }
  .brand__tagline {
    margin-top: 10px;
    font-family: "Lato", sans-serif; font-weight: 400;
    font-size: 22px; color: var(--tagline); letter-spacing: 0.2px;
  }

  .services {
    position: absolute; left: 0; right: 0; bottom: 40px;
    display: flex; justify-content: center; align-items: center; gap: 12px;
    font-family: "IBM Plex Mono", monospace; font-weight: 500;
    font-size: 15px; color: #ffffff; letter-spacing: 0.5px;
  }
  .services__dot { width: 8px; height: 8px; background: var(--orange); flex: none; }

  .mark {
    position: absolute; right: 44px; top: 88px;
    display: flex; align-items: center; gap: 10px;
  }
  .mark__square { width: 22px; height: 22px; background: var(--orange); }
  .mark__name {
    font-family: "Montserrat", sans-serif; font-weight: 800;
    font-size: 30px; color: var(--blue);
  }
  .mark__note {
    position: absolute; right: 44px; top: 132px;
    font-family: "IBM Plex Mono", monospace; font-weight: 500;
    font-size: 13px; color: var(--orange); letter-spacing: 0.4px;
  }

  .contact { position: absolute; left: 58px; top: 186px; }
  .contact__name {
    font-family: "Montserrat", sans-serif; font-weight: 800;
    font-size: 21px; letter-spacing: 1px; text-transform: uppercase;
    margin-bottom: 10px;
  }
  .contact__first { color: var(--blue); }
  .contact__last { color: var(--orange); }
  .contact__line {
    display: flex; align-items: center; gap: 8px;
    font-family: "Arimo", sans-serif; font-size: 17px; color: var(--ink);
    margin-bottom: 5px;
  }
  .contact__line svg { width: 17px; height: 17px; flex: none; }

  .bands { position: absolute; left: 0; bottom: 0; width: 620px; height: 80px; }
  .web {
    position: absolute; left: 30px; bottom: 24px;
    font-family: "Arimo", sans-serif; font-size: 17px; color: #ffffff;
    letter-spacing: 0.5px;
  }
</style>
</head>
<body>
<main class="canvas">
  <section class="card card--front" aria-label="Card front">
    <div class="brand">
      <div class="brand__name">VEXTORIAL</div>
      <div class="brand__tagline">developer of custom applications</div>
    </div>
    <div class="services">
      <span class="services__dot"></span>
      <span>Bitcoin education &amp; payment integration</span>
      <span class="services__dot"></span>
    </div>
  </section>

  <section class="card card--back" aria-label="Card back">
    <div class="mark">
      <span class="mark__square"></span>
      <span class="mark__name">VEXTORIAL</span>
    </div>
    <div class="mark__note">custom software + Bitcoin</div>

    <div class="contact">
      <div class="contact__name"><span class="contact__first">Dale</span> <span class="contact__last">Parker</span></div>
      <div class="contact__line">
        <svg viewBox="0 0 20 20" aria-hidden="true">
          <rect x="0" y="0" width="20" height="20" rx="3" fill="var(--orange)"/>
          <path d="M6 4.5l2.2 2.4-1.2 1.6c.8 1.8 2 3 3.8 3.8l1.6-1.2 2.4 2.2-1.3 1.9C9.6 15 5 10.4 4.1 5.8z" fill="#ffffff"/>
        </svg>
        (888) 555-VXTRL
      </div>
      <div class="contact__line">
        <svg viewBox="0 0 20 20" aria-hidden="true">
          <rect x="0" y="0" width="20" height="20" rx="3" fill="var(--orange)"/>
          <rect x="4" y="6" width="12" height="8.5" fill="none" stroke="#ffffff" stroke-width="1.4"/>
          <path d="M4 6l6 5 6-5" fill="none" stroke="#ffffff" stroke-width="1.4"/>
        </svg>
        dale@vextorial.com
      </div>
    </div>

    <svg class="bands" viewBox="0 0 620 80" aria-hidden="true">
      <polygon points="0,22 250,22 268,80 0,80" fill="var(--orange)"/>
      <polygon points="262,62 620,62 620,80 268,80" fill="var(--blue-deep)"/>
    </svg>
    <div class="web">www.vextorial.com</div>
  </section>
</main>
</body>
</html>
```